Brightway Haus Inc. Business Card Design

Brightway Haus Inc. is in search of a great clean design for our business cards!

Looking to incorporate our full logo and watermark on side one (however, I am open to having the text and watermark separated within the design.)

On side two, I am looking to have contact information (Name, Position, Phone #, Email, Website (www.thebrightwayhaus.ca). Can have the logo and/or watermark as part of the design if applicable.

Please add tagline "Where Shine Counts" on either side 1 or 2. This tagline can be in a sans serif, serif or cursive font as long as it compliments overall design. Capitalization can be title or sentence case depending on how it fits within the design.

Get creative!! Looking for a clean, crisp, premium design! Looking for a glossy card finish with spot UV features when printed. Cards will also be printed with rounded corners. Standard dimensions (3.5 x 2).

Target Market(s)

B2B - primary clients are business owners or property management corporations. (residential jobs are few and far between)

Industry/Entity Type

Business

Contact Information for Business Card

- clean, crisp design
- double sided
- spot UV accents and glossy finish upon printing
- standard business card size (3.5 x 2) with rounded corners
- please see project description for requirements per side

Font styles to use
Sans Serif

Requirements
Must have
• - adequate bleeds with print ready files
• - cohesive design elements between side 1 & 2
• - spot UV elements (can be on both sides or just one, use your discretion)
• - colour pallet should match the logo file provided
• - incorporate tagline "where shine counts" (this tagline can be in a serif or sans serif font as long as it is complimentary to the overall design.
Nice to have
• - Premium elements with a clean design
Should not have
• - Please omit cartoon or whimsical like designs, think premium.
• - Colours should not stray from the pallet of the provided logo.

```html
<!DOCTYPE html>
<html lang="en">
<head>
<meta charset="utf-8">
<title>Brightway Haus Inc. Business Card</title>
<link href="https://fonts.googleapis.com/css2?family=Open+Sans:wght@400;600;700;800&family=Caveat:wght@500&display=swap" rel="stylesheet">
<style>
  :root {
    --backdrop: #3a3a3c;
    --paper: #f2f2f2;
    --teal: #10b7ba;
    --navy: #1c2556;
    --silver: #b9b9b9;
    --white: #ffffff;
    --dark-card-top: #2a2b2d;
    --dark-card-bottom: #161718;
    --foil: #d9d9d9;
  }
  html, body {
    margin: 0;
    padding: 0;
    width: 1200px;
    height: 960px;
    overflow: hidden;
    background: var(--backdrop);
    font-family: "Open Sans", Arial, sans-serif;
  }
  .stage {
    position: relative;
    width: 1200px;
    height: 960px;
  }
  .card {
    position: absolute;
    width: 600px;
    height: 342px;
    border-radius: 22px;
    overflow: hidden;
    box-shadow: 0 4px 10px rgba(0,0,0,0.45);
  }
  .card-front {
    left: 314px;
    top: 129px;
    background: var(--paper);
  }
  .card-back {
    left: 311px;
    top: 488px;
    background: linear-gradient(180deg, var(--dark-card-top), var(--dark-card-bottom));
  }
  .front-waves {
    position: absolute;
    inset: 0;
  }
  .brand {
    position: absolute;
    display: flex;
    align-items: center;
    gap: 10px;
    font-weight: 800;
    letter-spacing: -0.5px;
    white-space: nowrap;
  }
  .brand-mark {
    display: block;
    width: 26px;
    height: 26px;
  }
  .card-front .brand {
    left: 46px;
    top: 82px;
    font-size: 27px;
    color: var(--navy);
  }
  .card-front .brand-mark { background: var(--teal); }
  .card-back .brand {
    left: 0;
    right: 0;
    top: 146px;
    justify-content: center;
    font-size: 36px;
    color: var(--foil);
  }
  .card-back .brand-mark {
    width: 34px;
    height: 34px;
    background: var(--foil);
  }
  .contact {
    position: absolute;
    right: 34px;
    top: 125px;
    text-align: right;
    color: var(--white);
  }
  .contact-name {
    margin: 0;
    font-size: 20px;
    font-weight: 700;
    line-height: 24px;
  }
  .contact-role {
    margin: 0 0 8px;
    font-size: 14px;
    font-weight: 700;
    line-height: 18px;
  }
  .contact-address {
    margin: 0 0 6px;
    font-size: 13px;
    line-height: 18px;
    font-style: normal;
  }
  .contact-list {
    list-style: none;
    margin: 0;
    padding: 0;
    font-size: 13px;
    line-height: 19.5px;
  }
  .contact-list li {
    display: flex;
    justify-content: flex-end;
    align-items: center;
    gap: 8px;
  }
  .contact-list svg {
    width: 13px;
    height: 13px;
    fill: var(--white);
    flex: none;
  }
  .tagline {
    position: absolute;
    left: 0;
    right: 0;
    top: 262px;
    margin: 0;
    text-align: center;
    font-family: "Caveat", cursive;
    font-weight: 500;
    font-size: 28px;
    color: var(--white);
  }
</style>
</head>
<body>
<main class="stage">
  <section class="card card-front" aria-label="Business card front">
    <svg class="front-waves" viewBox="0 0 600 342" aria-hidden="true">
      <path d="M380 72 C460 40 560 30 600 70 L600 80 C560 48 470 58 388 82 Z" fill="var(--silver)"/>
      <path d="M0 200 C10 250 60 292 150 292 C60 300 10 270 0 240 Z" fill="var(--navy)"/>
      <path d="M0 238 C40 284 110 300 180 286 C300 262 380 150 470 100 C530 68 580 68 600 96 L600 342 L0 342 Z" fill="var(--teal)"/>
      <path d="M0 238 C40 284 110 300 180 286 C300 262 380 150 470 100 C530 68 580 68 600 96" fill="none" stroke="var(--white)" stroke-width="3"/>
      <path d="M0 200 C15 255 70 296 180 292" fill="none" stroke="var(--white)" stroke-width="2"/>
    </svg>

    <div class="brand">
      <span class="brand-mark"></span>
      <span class="brand-name">BRIGHTWAY HAUS INC.</span>
    </div>

    <div class="contact">
      <p class="contact-name">MARA ELLISON</p>
      <p class="contact-role">CEO/FOUNDER</p>
      <address class="contact-address">1420 Harbor View Road<br>Juneau, Alaska 99801</address>
      <ul class="contact-list">
        <li>(907) 555-0182
          <svg viewBox="0 0 24 24" aria-label="Phone"><path d="M6.6 10.8a15.1 15.1 0 0 0 6.6 6.6l2.2-2.2c.3-.3.7-.4 1-.2 1.1.4 2.3.6 3.6.6.6 0 1 .4 1 1V20c0 .6-.4 1-1 1C10.6 21 3 13.4 3 4c0-.6.4-1 1-1h3.5c.6 0 1 .4 1 1 0 1.3.2 2.5.6 3.6.1.3 0 .7-.2 1z"/></svg>
        </li>
        <li>(907) 555-0147
          <svg viewBox="0 0 24 24" aria-label="Mobile"><path d="M7 1h10a2 2 0 0 1 2 2v18a2 2 0 0 1-2 2H7a2 2 0 0 1-2-2V3a2 2 0 0 1 2-2zm0 3v14h10V4zm5 15.5a1.2 1.2 0 1 0 0 2.4 1.2 1.2 0 0 0 0-2.4z"/></svg>
        </li>
        <li>(907) 555-0163
          <svg viewBox="0 0 24 24" aria-label="Fax"><path d="M6 2h12v6H6zM3 9h18a1 1 0 0 1 1 1v8h-4v4H6v-4H2v-8a1 1 0 0 1 1-1zm5 7v4h8v-4z"/></svg>
        </li>
        <li>mara@brightwayhaus.ca
          <svg viewBox="0 0 24 24" aria-label="Email"><path d="M2 5h20v14H2zm2 2v.5l8 5 8-5V7l-8 5z"/></svg>
        </li>
        <li>www.thebrightwayhaus.ca
          <svg viewBox="0 0 24 24" aria-label="Website"><path d="M12 2a10 10 0 1 0 0 20 10 10 0 0 0 0-20zm-1 17.9A8 8 0 0 1 4.2 10.2L9 15v1a2 2 0 0 0 2 2zm6.9-2.5A2 2 0 0 0 16 16h-1v-3a1 1 0 0 0-1-1H8v-2h2a1 1 0 0 0 1-1V7h2a2 2 0 0 0 2-2v-.4a8 8 0 0 1 2.9 12.8z"/></svg>
        </li>
      </ul>
    </div>
  </section>

  <section class="card card-back" aria-label="Business card back">
    <div class="brand">
      <span class="brand-mark"></span>
      <span class="brand-name">BRIGHTWAY HAUS INC.</span>
    </div>
    <p class="tagline">Where Shine Counts</p>
  </section>
</main>
</body>
</html>
```